Maple Roster Business Card for recruitment company

We are looking for a Business Card Design that incorporates our personal details and our busines name and logo. We are a specialized search consultancy that recruit Property and Construction professionals.
We would like a business card that stands out and is appealing to the Construction and Property industry as well.

Target Market(s)

people in the construction and property industry

Contact Information for Business Card

Business Name and logo

Font styles to use
Serif

Colors
0094D4
00A9DD
6FCCEA
C7EBF8
E9F6FB

Requirements
Must have
• Business name and logo as well as contact details
Should not have
• No photos of us please

```html
<!DOCTYPE html>
<html lang="en">
<head>
<meta charset="utf-8">
<title>Maple Roster Business Card</title>
<link rel="stylesheet" href="https://fonts.googleapis.com/css2?family=Questrial&family=Montserrat:wght@700&display=swap">
<style>
  :root {
    --stage: #2b2b2b;
    --card-front: #f7f7f7;
    --card-front-shade: #efefef;
    --ink: #0c3b52;
    --ink-soft: #3c3c3c;
    --card-back: #0a3d53;
    --card-back-deep: #062c3e;
    --mark-light: #d9e3e8;
  }
  * { margin: 0; padding: 0; box-sizing: border-box; }
  html, body {
    width: 1200px;
    height: 732px;
    overflow: hidden;
    background: var(--stage);
  }
  .canvas {
    position: relative;
    width: 1200px;
    height: 732px;
    background: var(--stage);
    font-family: "Questrial", sans-serif;
  }
  .card {
    position: absolute;
    top: 242px;
    width: 436px;
    height: 248px;
  }
  .card--front {
    left: 144px;
    background: linear-gradient(160deg, var(--card-front) 40%, var(--card-front-shade) 100%);
  }
  .card--back {
    left: 621px;
    background: linear-gradient(170deg, var(--card-back) 0%, var(--card-back-deep) 100%);
  }
  .wordmark {
    position: absolute;
    writing-mode: vertical-rl;
    transform: rotate(180deg);
    font-family: "Questrial", sans-serif;
    font-weight: 400;
    text-transform: uppercase;
    white-space: nowrap;
    line-height: 1;
    text-align: start;
  }
  .card--front .wordmark {
    left: 63px;
    top: 38px;
    height: 170px;
    font-size: 22px;
    letter-spacing: 0;
    color: var(--ink);
  }
  .card--back .wordmark {
    left: 390px;
    top: 19px;
    height: 209px;
    font-size: 27px;
    letter-spacing: 0;
    color: var(--mark-light);
  }
  .divider {
    position: absolute;
    left: 117px;
    top: 40px;
    width: 1px;
    height: 168px;
    background: var(--ink);
  }
  .details {
    position: absolute;
    left: 148px;
    top: 38px;
    color: var(--ink-soft);
  }
  .person-name {
    font-family: "Montserrat", sans-serif;
    font-weight: 700;
    font-size: 16px;
    color: var(--ink);
    line-height: 19px;
  }
  .person-role {
    font-size: 13px;
    line-height: 15px;
  }
  .contact-list {
    list-style: none;
    margin-top: 40px;
    font-size: 12.5px;
    line-height: 14.5px;
  }
  .contact-list .label {
    display: inline-block;
    width: 20px;
    font-weight: 700;
    color: var(--ink);
  }
  .location {
    position: absolute;
    left: 148px;
    top: 193px;
    font-size: 12.5px;
    color: var(--ink-soft);
  }
</style>
</head>
<body>
  <main class="canvas">
    <section class="card card--front" aria-label="Business card front">
      <div class="wordmark">Maple Roster</div>
      <div class="divider"></div>
      <div class="details">
        <h1 class="person-name">Clara Whitfield</h1>
        <p class="person-role">Director&nbsp; | &nbsp;Senior Search Consultant</p>
        <ul class="contact-list">
          <li><span class="label">T:</span>+64 27 480 2217</li>
          <li><span class="label">E:</span>clara@mapleroster.nz</li>
          <li><span class="label">W:</span>www.mapleroster.nz</li>
        </ul>
      </div>
      <p class="location">Auckland, New Zealand</p>
    </section>

    <section class="card card--back" aria-label="Business card back">
      <div class="wordmark">Maple Roster</div>
    </section>
  </main>
</body>
</html>
```